Bright and beautiful business card for a coach

I'm a personal and business coach based in Perth, Australia. I need a business card that whilst subtle and elegant, will stand out and appeal on a table full of cards.

My business name is Fern Mentoring and the business card must represent the warmth and brightness implied in the name, without being gimmicky. It must have a warmth and appeal and be easy to read.

I prefer clean, minimalist designs.

It must align with the feel of my website and socials: https://www.fernmentoring-example.com.au/
https://www.instagram.com/fernmentoringau/
https://www.facebook.com/fernmentoringau
Updates

Hi Designers Thank you so much for taking the time to submit designs. I wonder if I could have explained myself a little better. Most of the designs that have been submitted look rather formal and many have quite corporate looking embellishments on them (to my eye). I would like softer, warmer, more organic. I’m open to people playing about and being more abstract, using softer embellishments (e.g the line drawing flowers and grasses I’ve used in my socials) incorporating other colours from my palette or like the social icons in my email signature (in PDF), perhaps playing with size/oversize, playing with the bleed. Please don’t be constrained by what I’ve already done, it merely needs to compliment. I’m sorry if I’m not using the right words or have led you astray. I’m no designer, but I’ve done my website, socials, email signature etc all myself (my logo was a design contest) and I was really hoping for my business card to be something more creative than I could have made with a template. Reminder: No black cards/sides please. Thank you 😊

Target Market(s)

Individuals, most likely but not all female. Creative thinkers. Likely professionals.

Industry/Entity Type

Business & Personal Coach

Contact Information for Business Card

(Fern Mentoring Logo) Name: Greta Pellham; Title: Business & Personal Coach; Phone number: +61 (0)458 913307; Email: greta@fernmentoring-example.com.au; Website: https://fernmentoring-example.com.au; Social icons for Facebook, Instagram & LinkedIn: @fernmentoringAU. Optional strapline: "A thinking partner to help you cut through the noise"

Font styles to use
Sans Serif

Colors
00AB8E
00BBA5
67D7C9
C6EFE9
E9F9F6
59FF00
82FF00
B8FF75
E3FFCB
F4FFEA
FFC000
F8CF3A
FAE287
FDF2CF
FEFAEE

Requirements
Must have
• Must align with feel of my website and socials. Must have a pop of #FFC000 (possibly whole of one side, or at least a block). Bright or white background. Easy to read.
Nice to have
• Possibly incorporate the sunshine/grass picture I have used in website and socials - will upload.
Should not have
• Must not be black or dark. Not impersonal or corporate looking.

```html
<!DOCTYPE html>
<html lang="en">
<head>
<meta charset="utf-8">
<title>Fern Mentoring – Business Card</title>
<link rel="stylesheet" href="https://fonts.googleapis.com/css2?family=Lato:wght@400;700&family=Great+Vibes&display=swap">
<style>
  :root {
    --stage: #d4d4d4;
    --gold: #ffc000;
    --gold-deep: #d99f00;
    --cream: #fefaee;
    --text: #3a3a3a;
    --white: #ffffff;
    --grey: #8a8a8a;
    --leaf-dark: #3f6418;
    --leaf-mid: #6e9a26;
    --leaf-light: #a8c94a;
  }
  * { box-sizing: border-box; margin: 0; padding: 0; }
  html, body { width: 1200px; height: 800px; overflow: hidden; }
  body {
    background: var(--stage);
    font-family: "Lato", sans-serif;
    display: flex;
    align-items: center;
    justify-content: center;
    gap: 40px;
  }
  .card {
    position: relative;
    width: 560px;
    height: 320px;
    overflow: hidden;
    border-bottom: 3px solid var(--gold);
    box-shadow: 0 10px 24px rgba(0,0,0,.25);
  }

  /* Front */
  .card--front { background: var(--cream); }
  .front__photo {
    position: absolute; inset: 0;
    background: radial-gradient(ellipse at 35% 40%, var(--leaf-light), var(--leaf-mid) 45%, var(--leaf-dark) 100%);
    clip-path: polygon(0 0, 100% 0, 100% 28%, 0 60%);
  }
  .front__band {
    position: absolute; inset: 0;
    background: var(--cream);
    clip-path: polygon(0 60%, 100% 28%, 100% 100%, 0 100%);
  }
  .front__edge {
    position: absolute; inset: 0;
    background: var(--gold);
    clip-path: polygon(0 59%, 100% 27%, 100% 28.2%, 0 60.2%);
  }
  .brand {
    position: absolute;
    font-weight: 400;
    letter-spacing: 4px;
    text-transform: uppercase;
  }
  .card--front .brand {
    left: 60px; top: 90px;
    color: var(--white);
    font-size: 26px;
  }
  .person {
    position: absolute;
    left: 26px; bottom: 56px;
  }
  .person__name {
    font-family: "Great Vibes", cursive;
    color: var(--gold-deep);
    font-size: 34px;
    line-height: 1;
  }
  .person__title {
    color: var(--text);
    font-size: 15px;
    margin-top: 2px;
  }
  .contact {
    position: absolute;
    right: 22px; top: 150px;
    list-style: none;
    color: var(--text);
    font-size: 12.5px;
    line-height: 1.75;
  }
  .contact li { display: flex; align-items: center; gap: 7px; }
  .contact svg { width: 13px; height: 13px; flex: none; }
  .tagline {
    position: absolute;
    left: 0; right: 0; bottom: 14px;
    text-align: center;
    color: var(--gold-deep);
    font-size: 13px;
    font-weight: 700;
    letter-spacing: .5px;
    text-transform: uppercase;
  }

  /* Back */
  .card--back { background: var(--white); }
  .card--back .brand {
    left: 0; right: 0; top: 110px;
    text-align: center;
    color: var(--gold);
    font-size: 34px;
  }
  .socials {
    position: absolute;
    left: 90px; right: 90px; top: 220px;
    display: flex; align-items: center; gap: 8px;
  }
  .socials__rule { flex: 1; height: 1px; background: var(--grey); }
  .socials__dot {
    width: 22px; height: 22px; border-radius: 50%;
    background: var(--gold);
  }
</style>
</head>
<body>
  <section class="card card--front">
    <div class="front__photo" role="img" aria-label="Close-up photograph of sunlit green grass"></div>
    <div class="front__band"></div>
    <div class="front__edge"></div>
    <div class="brand">Fern Mentoring</div>
    <ul class="contact">
      <li>
        <svg viewBox="0 0 16 16" aria-hidden="true"><path fill="#ffc000" d="M3.6 1.5l2.3 2.6-1.3 1.8c.9 2 2.5 3.6 4.5 4.5l1.8-1.3 2.6 2.3-1.5 2.1C7.4 13.6 2.4 8.6 1.5 3z"/></svg>
        +61 (0)458 913307
      </li>
      <li>
        <svg viewBox="0 0 16 16" aria-hidden="true"><rect x="1" y="3" width="14" height="10" fill="#ffc000"/><path d="M1 3l7 6 7-6" fill="none" stroke="#fefaee" stroke-width="1.3"/></svg>
        greta@fernmentoring-example.com.au
      </li>
      <li>
        <svg viewBox="0 0 16 16" aria-hidden="true"><g fill="none" stroke="#ffc000" stroke-width="1.5"><circle cx="8" cy="8" r="6.5"/><ellipse cx="8" cy="8" rx="3" ry="6.5"/><path d="M1.5 8h13"/></g></svg>
        www.fernmentoring-example.com.au
      </li>
    </ul>
    <div class="person">
      <p class="person__name">Greta Pellham</p>
      <p class="person__title">Business &amp; Personal Coach</p>
    </div>
    <p class="tagline">A thinking partner to help you cut through the noise</p>
  </section>

  <section class="card card--back">
    <div class="brand">Fern Mentoring</div>
    <div class="socials">
      <span class="socials__rule"></span>
      <span class="socials__dot"></span>
      <span class="socials__dot"></span>
      <span class="socials__dot"></span>
      <span class="socials__rule"></span>
    </div>
  </section>
</body>
</html>
```